Logo + Business Card Design Project

We are looking at changing our logo and reprinting business cards.

Attached is a design concept for the logo (we have no hi res files for this).

The logo needs to be able to work standalone without the tagline.

We are happy for you to use this concept or design a new one. The existing concept is quite well liked.

We would also consider not having Solutions in the logo and just have Qorvel Systems Pty Ltd in the body text of the card.

We have a Tag Line that needs to go on all documentation / websites etc wherever the logo appears.

Tagline: Raising the bar

Our message to clients is that we have solutions that:

Qorvel Systems:
Raising the bar

Raising Revenue
Raising Profit
Raising Confidence

We would require the files in a High Res format for print and a scalable transparent format for web.
(We also need greyscale and monochrome files)
All source files need to be delivered with existing layers etc

A corporate guide with the logo usage and colours should be specified.

Suggestions:
The new logo has to have CMYK colours of 100 90 0 0

CMYK 100 90 0 0
RGB #21409A
Websafe #224499
Greyscale #414141

We would also need a business card layout designed.
Could be one sided or 2 sided. Will probably print matt cello 2 sides on 350gsm gloss

Should not have
• Lower case n in QVS.

```html
<!DOCTYPE html>
<html lang="en">
<head>
<meta charset="utf-8">
<title>Qorvel Systems – Logo and Business Card</title>
<link rel="stylesheet" href="https://fonts.googleapis.com/css2?family=PT+Sans:wght@400;700&family=PT+Sans+Narrow:wght@400;700&family=Niconne&display=swap">
<style>
  :root {
    --brand-blue: #21409a;
    --ink: #1a1a1a;
    --paper: #ffffff;
    --ghost: #e2e2e2;
    --stage: #2b2b2b;
    --rule: #555555;
  }
  * { margin: 0; padding: 0; box-sizing: border-box; }
  html, body { width: 849px; height: 1200px; overflow: hidden; }
  body { background: var(--stage); position: relative; font-family: "PT Sans", sans-serif; }

  .card {
    position: absolute;
    width: 360px; height: 220px;
    background: var(--paper);
    overflow: hidden;
  }
  .card--front-a { left: 45px; top: 150px; }
  .card--front-b { left: 45px; top: 430px; }
  .card--back { left: 432px; top: 345px; width: 372px; height: 215px; }

  .card__swoosh { position: absolute; inset: 0; width: 100%; height: 100%; }
  .card__swoosh path { fill: var(--brand-blue); }

  .wordmark {
    position: absolute;
    font-family: "PT Sans", sans-serif;
    font-weight: 700;
    color: var(--brand-blue);
    line-height: 1;
    letter-spacing: 2px;
  }
  .card--front-a .wordmark { left: 32px; top: 20px; font-size: 84px; }
  .card--front-b .wordmark { left: 32px; top: 38px; font-size: 84px; }

  .company-line {
    position: absolute;
    font-family: "PT Sans", sans-serif;
    color: var(--ink);
    text-transform: uppercase;
    white-space: nowrap;
  }
  .card--front-a .company-line { left: 36px; top: 114px; font-size: 14px; letter-spacing: 8px; font-weight: 700; }
  .card--front-b .company-line { left: 34px; top: 16px; font-size: 11px; letter-spacing: 6px; }

  .tagline {
    position: absolute;
    font-family: "Niconne", cursive;
    color: var(--ink);
    font-size: 27px;
    line-height: 1;
    white-space: nowrap;
  }
  .card--front-a .tagline { left: 36px; top: 146px; }
  .card--front-b .tagline { left: 36px; top: 134px; }

  .holder {
    position: absolute; right: 18px; text-align: right; color: var(--paper);
  }
  .holder__name { font-weight: 700; font-size: 14px; }
  .holder__role { font-size: 12.5px; }
  .card--front-a .holder { top: 166px; }
  .card--front-b .holder { top: 166px; }

  .card__ghost-mark {
    position: absolute; left: 24px; top: -8px;
    font-family: "PT Sans", sans-serif; font-weight: 700;
    font-size: 112px; line-height: 1; letter-spacing: 4px;
    color: var(--ghost);
  }
  .back__tagline {
    position: absolute; left: 56px; top: 46px;
    font-family: "Niconne", cursive; font-size: 30px; line-height: 1; color: var(--ink);
  }
  .back__promise {
    position: absolute; left: 104px; top: 86px;
    font-family: "PT Sans Narrow", sans-serif; font-weight: 700;
    font-size: 14px; letter-spacing: 0.5px; color: var(--brand-blue);
  }
  .contacts {
    position: absolute; top: 140px; left: 14px; right: 10px;
    display: flex;
    font-family: "PT Sans Narrow", sans-serif; font-size: 10.5px; color: var(--ink);
  }
  .contacts__col { display: grid; grid-template-columns: auto 1fr; column-gap: 16px; row-gap: 1px; }
  .contacts__col--phones { width: 140px; padding-right: 8px; border-right: 1px solid var(--rule); padding-bottom: 28px; }
  .contacts__col--online { padding-left: 12px; column-gap: 16px; align-content: start; }

  .logo-sheet { position: absolute; top: 800px; left: 0; width: 849px; height: 260px; }
  .logo-sheet__panel { position: absolute; left: 450px; top: 0; width: 399px; height: 260px; background: var(--paper); }
  .logo-sheet .wordmark { font-size: 72px; top: 90px; }
  .wordmark--reverse { left: 115px; color: var(--paper); }
  .wordmark--mono { left: 505px; color: #000000; }
</style>
</head>
<body>

  <section class="card card--front-a" aria-label="Business card front, version one">
    <svg class="card__swoosh" viewBox="0 0 360 220" aria-hidden="true"><path d="M90 220 Q180 145 360 114 L360 220 Z"/></svg>
    <div class="wordmark">QVS</div>
    <div class="company-line">Qorvel Systems</div>
    <div class="tagline">Raising the bar</div>
    <div class="holder">
      <div class="holder__name">Dana Whitcombe</div>
      <div class="holder__role">Project Director</div>
    </div>
  </section>

  <section class="card card--front-b" aria-label="Business card front, version two">
    <svg class="card__swoosh" viewBox="0 0 360 220" aria-hidden="true"><path d="M90 220 Q180 145 360 114 L360 220 Z"/></svg>
    <div class="company-line">Qorvel Systems Pty Ltd</div>
    <div class="wordmark">QVS</div>
    <div class="tagline">Raising the bar</div>
    <div class="holder">
      <div class="holder__name">Dana Whitcombe</div>
      <div class="holder__role">Project Director</div>
    </div>
  </section>

  <section class="card card--back" aria-label="Business card back">
    <div class="card__ghost-mark" aria-hidden="true">QVS</div>
    <div class="back__tagline">Raising</div>
    <div class="back__promise">GROWTH, MARGIN, TRUST</div>
    <div class="contacts">
      <div class="contacts__col contacts__col--phones">
        <span>Phone</span><span>+61 2 5550-1200</span>
        <span>Support</span><span>+61 2 5550-1233</span>
        <span>Fax</span><span>+61 2 5550-1201</span>
        <span>Mobile</span><span>0400 555 018</span>
      </div>
      <div class="contacts__col contacts__col--online">
        <span>Email</span><span>dana.whitcombe@qorvel.com.au</span>
        <span>Web</span><span>www.qorvel.com.au</span>
        <span>Address</span><span>118/42 Larkfield Road<br>Brookvale NSW 2100</span>
      </div>
    </div>
  </section>

  <section class="logo-sheet" aria-label="Logo in reverse and monochrome">
    <div class="logo-sheet__panel"></div>
    <div class="wordmark wordmark--reverse">QVS</div>
    <div class="wordmark wordmark--mono">QVS</div>
  </section>

</body>
</html>
```